Business Card - high end, modern health care

Hey designers!

We need a double sided business card for the boutique, cutting edge physical therapy rehabilitation centre in Sydney's Northern Beaches.

With the most qualified physios in the area The Harbourview Motion Clinic does what other physiotherapy practices do not, we take our time with our patients giving them longer appointments, better physios and therefor faster results!

We guarantee that the service people receive at THMC will be unparalleled.

Hence we need a business card to reflect our modern, boutique, high end service. The final design needs to reflect that we are in a class of our own yet with the feel of beachside retreat.

Below I have attached our logo in both blue on white and white on blue. The exact colour is;
and the font that we have used in our logo is Tex Gyre Aventador.

I like the idea of the blue as the main colour as it is more eye catching and our signage onto the main road will be in this blue and in the interest of consistency across marketing the blue needs to be a part of the design. However I would appreciate a few designs onto a wooden background as this is a visual theme within the fitout of the practice.

The design needs to be of standard size (91x55mm).

Target Market(s)

We target people who have an end outcome in mind and those who have had poor experiences with other providers and ensure that everyone gets the care that they deserve with a premium service that is tailored to the individuals circumstances. As a premium service, the target market is highly educated, business and tech savvy with the additional target market of elderly people who have self funded their retirement and see value in paying for the best ongoing rehabilitation to maintain independence.

Industry/Entity Type

Physical Therapy

Contact Information for Business Card

Name, designation( Titled Musculoskeletal Physiotherapist... there will also be those in the company that have multiple designations ie 5 or 6 words long), phone number, email, facebook, instagram, address

Font styles to use
Sans Serif

Colors

Designer to choose colors to be used in the design.

Requirements
Must have
• Front - The logo as large as possible, blue or wooden theme, and all of the important details.
• Back - A blank space/lines on which to write appointment times (no "Appointment, date, time" etc.)
Nice to have
• facebook url
• logos for facebook and instagram
• Mini logos for the phone and email?

```html
<!DOCTYPE html>
<html lang="en">
<head>
<meta charset="utf-8">
<title>The Harbourview Motion Clinic – Business Card</title>
<link href="https://fonts.googleapis.com/css2?family=Roboto:wght@400&family=Roboto+Condensed:wght@400;700&display=swap" rel="stylesheet">
<style>
  :root {
    --backdrop: #1e1e1e;
    --card-front: #f1f1f1;
    --card-back: #ffffff;
    --brand-blue: #0a55a6;
    --band-grey: #505257;
    --text-grey: #4a4a4a;
    --rule-grey: #5a5a5a;
    --divider: #c9c9c9;
    --faint-blue: #edf1f8;
  }
  * { margin: 0; padding: 0; box-sizing: border-box; }
  html, body { width: 1200px; height: 960px; overflow: hidden; }
  body { background: var(--backdrop); position: relative; font-family: "Roboto", sans-serif; }

  .card { position: absolute; width: 599px; height: 342px; border-radius: 16px; overflow: hidden; }
  .card-front { left: 322px; top: 108px; background: var(--card-front); }
  .card-back { left: 320px; top: 493px; background: var(--card-back); }

  /* front */
  .brand-mark { position: absolute; left: 106px; top: 76px; width: 148px; height: 148px; border-radius: 50%; background: var(--brand-blue); }
  .brand-name { position: absolute; left: 70px; top: 232px; width: 220px; text-align: center;
    font-family: "Roboto Condensed", sans-serif; font-weight: 700; font-size: 17px; line-height: 19px;
    letter-spacing: 0.5px; color: var(--brand-blue); text-transform: uppercase; }
  .divider { position: absolute; left: 290px; top: 75px; width: 2px; height: 197px; background: var(--divider); }

  .details { position: absolute; left: 319px; top: 72px; color: var(--text-grey); }
  .person-name { font-family: "Roboto Condensed", sans-serif; font-weight: 700; font-size: 22px; line-height: 24px; color: var(--brand-blue); }
  .person-title { font-family: "Roboto Condensed", sans-serif; font-size: 15px; line-height: 18px; margin-top: 1px; }
  .address { font-size: 14px; line-height: 18px; margin-top: 13px; }
  .contacts { list-style: none; margin-top: 11px; }
  .contacts li { display: flex; align-items: center; font-size: 14px; line-height: 19px; }
  .contacts svg { width: 13px; height: 13px; margin-right: 9px; flex: none; fill: var(--brand-blue); }

  .band-blue { position: absolute; left: 0; bottom: 0; width: 372px; height: 14px; background: var(--brand-blue); clip-path: polygon(0 0, 100% 0, 97.5% 100%, 0 100%); }
  .band-grey { position: absolute; right: 0; bottom: 0; width: 233px; height: 14px; background: var(--band-grey); clip-path: polygon(4% 0, 100% 0, 100% 100%, 0 100%); }

  /* back */
  .faint-ring { position: absolute; left: 151px; top: 30px; width: 298px; height: 298px; border-radius: 50%; border: 24px solid var(--faint-blue); }
  .appt-row { position: absolute; left: 32px; width: 527px; display: flex; align-items: flex-end;
    font-family: "Roboto", sans-serif; font-size: 16px; color: var(--text-grey); }
  .appt-row .fill { border-bottom: 1px solid var(--rule-grey); margin: 0 5px 4px; height: 1px; }
  .appt-row .fill-date { width: 262px; }
  .appt-row .fill-time { width: 114px; }
  .appt-row-1 { top: 40px; }
  .appt-row-2 { top: 84px; }
  .note-line { position: absolute; left: 35px; width: 524px; height: 1px; background: var(--rule-grey); }
</style>
</head>
<body>

<section class="card card-front" aria-label="Business card front">
  <div class="brand-mark" aria-hidden="true"></div>
  <div class="brand-name">The Harbourview<br>Motion Clinic</div>
  <div class="divider"></div>

  <div class="details">
    <p class="person-name">LIAM CARTER</p>
    <p class="person-title">CEO/FOUNDER</p>
    <p class="address">42 Pittwater Road<br>Manly, NSW 2095</p>
    <ul class="contacts">
      <li><svg viewBox="0 0 24 24"><path d="M6.6 10.8a15.1 15.1 0 0 0 6.6 6.6l2.2-2.2c.3-.3.7-.4 1-.2 1.1.4 2.3.6 3.6.6.6 0 1 .4 1 1V20c0 .6-.4 1-1 1A17 17 0 0 1 3 4c0-.6.4-1 1-1h3.5c.6 0 1 .4 1 1 0 1.3.2 2.5.6 3.6.1.3 0 .7-.2 1z"/></svg>612 555 0148</li>
      <li><svg viewBox="0 0 24 24"><path d="M2 5h20v14H2z M3.5 6.5 12 12.5l8.5-6" fill="none" stroke="#0a55a6" stroke-width="2"/><path d="M2 5h20v2l-10 7L2 7z"/><rect x="2" y="5" width="20" height="14"/></svg>liam@harbourviewmotion.com</li>
      <li><svg viewBox="0 0 24 24"><circle cx="12" cy="12" r="10"/><path d="M2 12h20M12 2c3 3 3 17 0 20M12 2c-3 3-3 17 0 20" fill="none" stroke="#f1f1f1" stroke-width="1.5"/></svg>www.harbourviewmotion.com</li>
      <li><svg viewBox="0 0 24 24"><rect x="2" y="2" width="20" height="20"/></svg>/harbourviewmotion</li>
      <li><svg viewBox="0 0 24 24"><rect x="2" y="2" width="20" height="20" rx="5"/></svg>@harbourviewmotion</li>
    </ul>
  </div>

  <div class="band-blue"></div>
  <div class="band-grey"></div>
</section>

<section class="card card-back" aria-label="Business card back, appointment lines">
  <div class="faint-ring" aria-hidden="true"></div>
  <div class="appt-row appt-row-1"><span>Date</span><span class="fill fill-date"></span><span>Time</span><span class="fill fill-time"></span><span>am/pm</span></div>
  <div class="appt-row appt-row-2"><span>Date</span><span class="fill fill-date"></span><span>Time</span><span class="fill fill-time"></span><span>am/pm</span></div>
  <div class="note-line" style="top:139px"></div>
  <div class="note-line" style="top:179px"></div>
  <div class="note-line" style="top:219px"></div>
  <div class="note-line" style="top:259px"></div>
  <div class="note-line" style="top:299px"></div>
</section>

</body>
</html>
```